Design and Renovation Company Luxury Business Card

I want to create a luxury business card for a Design and Renovation Firm . We will use our current logo. The company name is 528BUILDA. We do not want anything standard. We need a very unique concept.
Please see uploaded inspiration. I really like the textured paper option. I would like the card to be thick with debossing, and/or embossing options. The logo has orange in it but I would like to see the card with and without the orange. I think the orange may make the company feel less high-end. The goal is to elevate the logo not match its vibe per se of the logo. We want something very unique, not standard at all!
I would like a space for :
Logo,
Name,
Position,
Email,
Office number,
Website Address,
Business Address,
Thank you!
Have fun!
Target Market(s)
Home owners Age 35 +
Industry/Entity Type
Design and Renovation
Contact Information for Business Card
Logo, Name, Position, Email, Office number, Website Address, Business Address,.
Colors
Designer to choose colors to be used in the design.
Requirements
Must have
- A luxury designer feel. Must be black or dark grey but open to other luxury ideas.
Nice to have
- Gold, silver, black embossing or debossing. Textured paper design.
Should not have
- A cheap look and feel.

```html
<!DOCTYPE html>
<html lang="en">
<head>
<meta charset="utf-8">
<title>528BUILDA Business Card</title>
<link href="https://fonts.googleapis.com/css2?family=Ubuntu:wght@400;500&display=swap" rel="stylesheet">
<style>
  :root {
    --backdrop: #7f7f7f;
    --card-white: #ffffff;
    --card-black: #141416;
    --ink: #111111;
    --accent: #f39221;
    --deboss: #4a4a4d;
  }
  * { margin: 0; padding: 0; box-sizing: border-box; }
  html, body { width: 1200px; height: 855px; overflow: hidden; }
  body { background: var(--backdrop); position: relative; font-family: "Ubuntu", sans-serif; }

  .card { position: absolute; }
  .card-front { left: 129px; top: 140px; width: 326px; height: 573px; background: var(--card-white); }
  .card-back { left: 505px; top: 384px; width: 579px; height: 329px; background: var(--card-black); }

  .brand-name { position: absolute; font-family: "Ubuntu", sans-serif; font-weight: 500; line-height: 1; white-space: nowrap; }
  .card-front .brand-name { left: 34px; top: 62px; font-size: 38px; color: var(--ink); }
  .card-back .brand-name { left: 0; right: 0; top: 130px; text-align: center; font-size: 64px; color: var(--deboss); }

  .person-name { position: absolute; left: 30px; top: 317px; font-size: 29px; font-weight: 500; line-height: 1.1; color: var(--accent); }
  .person-role { position: absolute; left: 30px; top: 348px; font-size: 13px; line-height: 1.2; color: var(--ink); }
  .divider { position: absolute; left: 30px; width: 17px; height: 1.5px; background: var(--accent); }
  .divider-top { top: 383px; }
  .divider-bottom { top: 460px; }
  .address { position: absolute; left: 30px; top: 405px; font-size: 13px; line-height: 16.5px; color: var(--ink); }

  .contact-list { position: absolute; left: 29px; top: 483px; list-style: none; }
  .contact-item { display: flex; align-items: center; height: 20.5px; font-size: 13px; color: var(--ink); }
  .contact-icon { width: 11px; height: 11px; margin-right: 10px; flex: none; }
</style>
</head>
<body>
  <section class="card card-front">
    <p class="brand-name">528BUILDA</p>

    <h1 class="person-name">DORIAN VALE</h1>
    <p class="person-role">Medical Director</p>
    <span class="divider divider-top"></span>
    <p class="address">418 Harlow Crescent Suite 12<br>Brookhaven, New York 11719</p>
    <span class="divider divider-bottom"></span>

    <ul class="contact-list">
      <li class="contact-item">
        <svg class="contact-icon" viewBox="0 0 12 12" aria-hidden="true"><path d="M2.5 1 L4.5 1 L5.3 3.4 L4 4.4 Q5 6.8 7.6 8 L8.6 6.7 L11 7.5 L11 9.5 Q11 11 9.5 11 Q1 10.5 1 2.5 Q1 1 2.5 1 Z" fill="none" stroke="#f39221" stroke-width="1.3"/></svg>
        <span>(000)555-0148</span>
      </li>
      <li class="contact-item">
        <svg class="contact-icon" viewBox="0 0 12 12" aria-hidden="true"><rect x="0.5" y="2" width="11" height="8" fill="#f39221"/><path d="M1 2.5 L6 6.5 L11 2.5" fill="none" stroke="#fff" stroke-width="1.1"/></svg>
        <span>hello@528builda.com</span>
      </li>
      <li class="contact-item">
        <svg class="contact-icon" viewBox="0 0 12 12" aria-hidden="true"><circle cx="6" cy="6" r="5.3" fill="#f39221"/><path d="M6 0.7 Q3 6 6 11.3 M6 0.7 Q9 6 6 11.3 M0.7 6 H11.3" fill="none" stroke="#fff" stroke-width="0.9"/></svg>
        <span>www.528builda.com</span>
      </li>
    </ul>
  </section>

  <section class="card card-back">
    <p class="brand-name">528BUILDA</p>
  </section>
</body>
</html>
```